Verpackungen Geschenkbox
Eine völlig unkomplizierte und tolle Zusammenarbeit. Und ein ganz tolles Ergebnis. Vielen Dank auch hier noch einmal : )
Zielgruppe
In unserem Studio können Kunden Keramik bemalen
Aufgabenstellung
Ich hätte gerne eine Vorlage für einen Aufkleber, den ich auf eine Verschenkbox machen kann. Diese Geschenkbox werde ich mit einer Rohkeramik füllen, zusätzlich alle Materialien die dafür benötigt werden, wie z.B. Glasuren, Pinsel etc. Diese Boxen sind fertig gerichtet, können direkt gekauft werden und die bemalte Keramik uns wieder zum Brennen gebracht werden. Der Aufkleber dazu soll zu unserem ganzen Stil passen und es soll unser Logo enthalten sein. Es soll zum Kaufen annimieren, aber nicht übertrieben sein. Eher klar auch in den Farben.
Der Aufkleber sollte max. 10 cm groß sein. Der Karton ist viereckig, unterschiedlich groß, so dass eine Tasse, Müslischale oder Teller reinpasst, mit ein paar kleine Fabdosen, Pinsel und anderes Materialien wie Schwamm oder Punktewerkzeug. Achtung, es ist keine Töpferei

```html
<!DOCTYPE html>
<html lang="de">
<head>
<meta charset="utf-8">
<title>Keramik-Malbox Aufkleber</title>
<link rel="stylesheet" href="https://fonts.googleapis.com/css2?family=Libre+Baskerville:wght@700&family=Itim&family=Arimo&display=swap">
<style>
  :root {
    --teal: #177a87;
    --white: #ffffff;
    --tape: #d4d4d4;
    --art-light: #eef3f4;
    --art-mid: #d7dcdd;
  }
  html, body {
    margin: 0;
    padding: 0;
    width: 1200px;
    height: 959px;
    overflow: hidden;
    background: var(--white);
  }
  .sticker {
    display: block;
    width: 1200px;
    height: 959px;
  }
  .title {
    font-family: "Libre Baskerville", Georgia, serif;
    font-weight: 700;
    fill: var(--white);
    font-size: 78px;
    letter-spacing: 1px;
  }
  .subtitle {
    font-family: "Itim", cursive;
    fill: var(--white);
    font-size: 52px;
  }
  .tape-text {
    font-family: "Libre Baskerville", Georgia, serif;
    font-weight: 700;
    fill: var(--teal);
  }
  .label {
    font-family: "Itim", cursive;
    fill: var(--teal);
    font-size: 40px;
  }
  .arrow {
    fill: none;
    stroke: var(--teal);
    stroke-width: 3;
    stroke-linecap: round;
    stroke-linejoin: round;
  }
  .info {
    font-family: "Arimo", Arial, sans-serif;
    fill: var(--teal);
    font-size: 20px;
    letter-spacing: 0.3px;
  }
  .brand-name {
    font-family: "Arimo", Arial, sans-serif;
    fill: var(--teal);
    font-size: 32px;
  }
</style>
</head>
<body>
<svg class="sticker" viewBox="0 0 1125 899" xmlns="http://www.w3.org/2000/svg">
  <defs>
    <clipPath id="sticker-shape">
      <rect x="42" y="37" width="1040" height="820" rx="44"/>
    </clipPath>
    <linearGradient id="art-fill" x1="0" y1="0" x2="0" y2="1">
      <stop offset="0" stop-color="var(--art-light)"/>
      <stop offset="1" stop-color="var(--art-mid)"/>
    </linearGradient>
  </defs>

  <!-- sticker body -->
  <g clip-path="url(#sticker-shape)">
    <rect class="body-band" x="42" y="37" width="1040" height="820" fill="var(--teal)"/>
    <rect class="footer-band" x="42" y="712" width="1040" height="150" fill="var(--white)"/>
  </g>
  <rect class="sticker-outline" x="42" y="37" width="1040" height="820" rx="44" fill="none" stroke="var(--teal)" stroke-width="3"/>

  <!-- headline -->
  <text class="title" x="560" y="160" text-anchor="middle">KERAMIK-MALBOX</text>
  <text class="subtitle" x="552" y="232" text-anchor="middle">Für deine kreative Auszeit!</text>

  <!-- stage ellipse -->
  <ellipse class="stage" cx="568" cy="470" rx="432" ry="215" fill="var(--white)"/>
  <ellipse class="stage-ring" cx="568" cy="470" rx="422" ry="206" fill="none" stroke="var(--teal)" stroke-width="3"/>

  <!-- box contents illustration -->
  <rect class="box-illustration" role="img" aria-label="Illustration: Karton mit Rohkeramik-Tasse, Glasurdosen und Pinseln"
        x="370" y="412" width="450" height="236" rx="14" fill="url(#art-fill)"/>

  <!-- labels with arrows -->
  <text class="label" x="222" y="502" transform="rotate(-20 222 502)">Rohkeramik</text>
  <path class="arrow" d="M300 497 Q335 480 362 476 M350 468 L362 476 L352 487"/>

  <text class="label" x="506" y="392" transform="rotate(-4 506 392)">Glasuren</text>
  <path class="arrow" d="M668 394 Q695 405 688 436 M678 426 L688 436 L695 424"/>

  <text class="label" x="858" y="478" transform="rotate(12 858 478)">Pinsel</text>
  <path class="arrow" d="M846 418 Q815 412 800 438 M797 424 L800 438 L812 432"/>

  <!-- tape banner -->
  <g class="tape" transform="rotate(-9 265 335)">
    <path d="M72 285 L460 278 L466 300 L458 318 L468 340 L460 362 L466 386 L82 392 L76 370 L86 350 L74 330 L84 308 Z" fill="var(--tape)"/>
    <text class="tape-text" x="268" y="334" text-anchor="middle" font-size="32">ALLES DRIN–</text>
    <text class="tape-text" x="268" y="368" text-anchor="middle" font-size="24">EINFACH LOSLEGEN</text>
  </g>

  <!-- brand -->
  <text class="brand-name" x="562" y="784" text-anchor="middle">Sunny Clay</text>

  <!-- footer info -->
  <text class="info" x="237" y="771" text-anchor="middle">Alle Materialien inklusive</text>
  <text class="info" x="237" y="797" text-anchor="middle">Ab X Jahren geeignet</text>
  <text class="info" x="237" y="823" text-anchor="middle">Keine Vorkenntisse nötig</text>

  <text class="info" x="918" y="771" text-anchor="middle">Bemalen,</text>
  <text class="info" x="918" y="797" text-anchor="middle">zurückbringen und</text>
  <text class="info" x="918" y="823" text-anchor="middle">brennen lassen.</text>
</svg>
</body>
</html>
```